Wine Label Design-Hollow Creek Vineyard

Hollow Creek Vineyard is in the Barossa Valley in South Australia. The Barossa is recognized as Australia's premier wine region, producing Australia's icon wines and some " new takes on traditional".
This family owned and operated vineyard grows some exceptionally high quality fruit. Most of the fruit is sold and used for some of Australia's most iconic wines. Small quantities are retained by the owners for some wines with very limited availability. (Wines were previously sold as Brackwell Vineyards Hollow Creek ( Shiraz, Cabernet etc).

The wines will in the future be labeled simply ‘Hollow Creek Vineyard’. The label will launch this new identity for the single family single vineyard and its high quality wines which are a true expression of the vineyard and derive from the Hollow Creek common to this ancient area (800-2000 million years old).
The label should reflect
• Single vineyard, family owned
• vines in very old rock & soils
• High quality & reliability
• Edgy but true, design based thinking (Please note:blue is generally seen as an unacceptable colour for a wine label?? Don’t ask me why)

The wines will be sold mostly direct in Australia ( ie not through retail stores), with limited export to Asia, Scandinavia and Canada.
There are three quality levels and price points in the portfolio
1. Entry level premium for everyday drinking for discriminating drinkers-approx AUD20
2. Super Premium-approx AUD30
3. Limited Release ultlra premium-AUD75-90?
We envisage three variations on the label but with an obvious & common design element. This design element should be able to be used for corporate identification and promotion
The paper stock will be waterproof and self adhesive. Our preference is for designs that engage the user by appealing to both sight and touch. It is preferred that textures be added eg embossing, high build varnish etc-rather than be a facet of the stock itself.
For information on statutory label requirements refer to www.vintnerregistry-example.com . In brief
o Front label need not show any mandatory information. However we would prefer Variety, Barossa Valley, Year and alcohol to be shown on the front label
o Back label should show all mandatories and allow for a bar code
Updates

Project Deadline Extended
Reason: I've had a problem with my wireless broadband account and reception has been intermittent to say the least to the extent that I switched off at the weekend. Just going downtown now for a 'polite discussion' with my service provider.

Project Deadline Extended
Reason: I have receiver insufficient designs of quality which we would consider. Too many designs have a "cut and paste" appearance - too few exhibit an original art/design element which truly identifies the product.

Gals & Guys

most of the designs submitted lack punch and originality and are totally unmemorable.
Please-get on Searcho or whatever enter "Wine Label Designs" and do some research b4 u waste your time and mine. Formulaic cut and paste will not win the day. That's not to say that cut and paste can't work-but it must have some originality, impact and command attention. Please surprise me.

Following on from a question from a designer about who is our competition and what we are looking for I sent the following 
"I don't think I can add anything new. Read the brief and comments again and research wine labels on the web. In 30 minutes you'll get a good idea of the creative edgy designs in the industry. There are a plethora of collections. Our competition-anyone with a label. In 2010 there were over 2400 "producers" in other words 2400 producers with at least one label. In fact there are over 25000 Australian wines and then the numerous imported wines.

Target Market(s)

$20 people who budget everyday but have graduated from drinking 'entry level' wines. These people will likely fit into Cat. (b) in the $30 wine

$30 (a) will not over-compromise on some everyday discretionary expenditure.(b) might buy for special occasions

$70-$90 Professional/successful people with high disposable/discretionary income not particularly worried about recession. wine geeks.

Industry/Entity Type

Retail

Requirements
Must have
• identifiable element across range of wines

```html
<!DOCTYPE html>
<html lang="en">
<head>
<meta charset="utf-8">
<title>Hollow Creek Vineyards – Shiraz Label Set</title>
<link rel="stylesheet" href="https://fonts.googleapis.com/css2?family=Mystery+Quest&family=Gochi+Hand&family=Parisienne&display=swap">
<style>
  :root {
    --page: #ffffff;
    --stage-light: #e6f0f0;
    --stage-mid: #a9b9bd;
    --stage-dark: #44575c;
    --gold: #d4ad3a;
    --gold-dark: #a8862a;
    --cream: #d8c77c;
    --cream-light: #e6d898;
    --wine: #a51d2c;
    --wine-dark: #7e1220;
    --ink: #231c14;
    --white: #f6f1e6;
    --swirl-brown: #9a6a45;
    --swirl-blue: #9eb2b8;
    --vista-sky: #b8c4cc;
    --vista-vine: #4d7a2f;
  }
  * { box-sizing: border-box; margin: 0; padding: 0; }
  html, body { width: 1200px; height: 951px; overflow: hidden; background: var(--page); }
  .canvas { position: relative; width: 1200px; height: 951px; }
  .stage {
    position: absolute; left: 52px; top: 58px; width: 1080px; height: 845px;
    background: linear-gradient(135deg, var(--stage-light) 0%, var(--stage-mid) 55%, var(--stage-dark) 100%);
  }
  .stage-motif {
    position: absolute; left: 400px; top: 150px; width: 320px; height: 520px;
    border-radius: 50%;
    background: radial-gradient(ellipse, rgba(120,140,146,0.28), rgba(120,140,146,0) 70%);
  }
  .gold-frame { position: absolute; background: var(--gold); border: 2px solid var(--gold-dark); }
  .wine-band {
    position: absolute; background: var(--wine);
    border: 3px solid var(--cream-light);
    box-shadow: inset 0 0 10px var(--wine-dark);
    display: flex; flex-direction: column; align-items: center; justify-content: center;
  }
  .brand-name {
    font-family: "Mystery Quest", cursive; color: var(--white);
    text-align: center; line-height: 1.05;
  }
  .rock-accent {
    position: absolute; background: linear-gradient(135deg, var(--white), var(--swirl-blue));
    border-radius: 40% 60% 45% 55%;
  }

  /* corporate mark */
  .brand-tag { left: 450px; top: 90px; width: 252px; height: 76px; padding: 4px; }
  .brand-tag .wine-band { inset: 4px; }
  .brand-tag .brand-name { font-size: 23px; }

  /* front label */
  .front-label { left: 202px; top: 243px; width: 312px; height: 464px; padding: 8px;
    box-shadow: 4px 6px 10px rgba(0,0,0,0.35); }
  .front-face { position: absolute; inset: 8px; background: var(--cream); }
  .front-label .logo-band { left: 35px; top: 18px; width: 235px; height: 88px; }
  .front-label .brand-name { font-size: 24px; }
  .swirl-strip {
    position: absolute; left: 0; right: 0; top: 187px; height: 53px;
    background: linear-gradient(90deg, var(--swirl-brown), rgba(154,106,69,0.55), var(--swirl-brown));
    opacity: 0.75;
  }
  .vista-oval {
    position: absolute; left: 59px; top: 118px; width: 143px; height: 217px;
    border-radius: 50%; border: 5px solid var(--gold-dark);
    background: linear-gradient(180deg, var(--vista-sky) 0%, var(--vista-sky) 38%, var(--vista-vine) 62%, #3a5a24 100%);
  }
  .vintage-band { left: 66px; top: 344px; width: 212px; height: 102px;
    outline: 4px solid var(--gold); }
  .vintage-band p {
    font-family: "Parisienne", cursive; color: var(--white); font-size: 25px; line-height: 1.15;
  }
  .vintage-band .year { margin-left: 28px; }

  /* back label */
  .back-upper { left: 671px; top: 241px; width: 306px; height: 200px; padding: 6px; }
  .back-upper-face { position: absolute; inset: 6px; background: var(--cream);
    padding: 6px 12px; font-family: "Gochi Hand", cursive; color: var(--ink); }
  .back-title { color: var(--white); font-size: 16px; text-align: center; letter-spacing: 0.5px; }
  .back-story { margin-top: 6px; font-size: 12.5px; line-height: 1.15; text-align: center; }
  .back-story .initial { color: var(--wine); font-size: 16px; }
  .drinks { position: absolute; right: 10px; bottom: 6px; font-size: 11px; color: var(--white);
    text-align: right; line-height: 1.1; }
  .back-vista {
    position: absolute; left: 772px; top: 411px; width: 89px; height: 80px; border-radius: 50%;
    border: 4px solid var(--gold-dark); z-index: 2;
    background: linear-gradient(180deg, var(--vista-sky) 40%, var(--vista-vine) 70%);
  }
  .back-lower { left: 668px; top: 489px; width: 310px; height: 214px; padding: 6px; }
  .back-pattern { position: absolute; inset: 6px;
    background: linear-gradient(120deg, var(--swirl-brown), var(--swirl-blue) 45%, var(--swirl-brown) 90%); }
  .mandatory { position: absolute; left: 10px; top: 63px; width: 178px;
    font-family: "Gochi Hand", cursive; font-size: 12.5px; line-height: 1.05; color: var(--ink); }
  .mandatory address { font-style: normal; text-align: right; margin-bottom: 10px; }
</style>
</head>
<body>
<main class="canvas">
  <div class="stage">
    <div class="stage-motif" role="img" aria-label="Faint large decorative motif"></div>
  </div>

  <section class="gold-frame brand-tag" aria-label="Hollow Creek brand mark">
    <div class="wine-band">
      <p class="brand-name">Hollow Creek<br>Vineyards</p>
    </div>
  </section>

  <section class="gold-frame front-label" aria-label="Front label">
    <div class="front-face">
      <div class="swirl-strip" role="img" aria-label="Decorative swirl band"></div>
      <div class="wine-band logo-band">
        <p class="brand-name">Hollow Creek<br>Vineyards</p>
      </div>
      <div class="vista-oval" role="img" aria-label="Painted view of vineyard rows under a cloudy sky"></div>
      <div class="wine-band vintage-band">
        <p>Barossa Valley</p>
        <p>Shiraz <span class="year">2012</span></p>
      </div>
    </div>
  </section>

  <section class="gold-frame back-upper" aria-label="Back label story">
    <div class="back-upper-face">
      <h2 class="back-title">Shiraz 2012 Barossa Valley</h2>
      <p class="back-story"><span class="initial">O</span>ur wines are planted on areas which are characterized by enormous quantities of shattered shale, slate, and limestone based rock, which are major components in the unique flavor and our tight structure and minerality with abundant and generous fruit. Drinking well from the release and getting better from 2 to 12 years.</p>
      <p class="drinks">8.3 standard<br>drinks</p>
    </div>
  </section>

  <div class="back-vista" role="img" aria-label="Small painted vineyard view"></div>

  <section class="gold-frame back-lower" aria-label="Back label mandatory information">
    <div class="back-pattern" role="img" aria-label="Decorative swirl pattern in brown and grey-blue"></div>
    <div class="mandatory">
      <address>Hollow Creek Vineyards<br>Lot 7 Kestrel Ridge Road<br>Tanunda North, SA<br>5399 Australia</address>
      <p>750 ml<br>Wine of Australia<br>13.5 % alc/vol<br>Contains sulfites<br>Produced with milk products</p>
    </div>
  </section>
</main>
</body>
</html>
```